Detail Shop Business card design

i need a business card design for my new detailing company called 'Brisk's Polish Works'. i want an all black and white design . simple, direct and to the point. i want the designer to choose a fitting font to match the logothe front should have logo, address, phone and email and the back side should have a slogan and text indicating that we offer services on anything including cars, trucks, motorcycles and RVs. slogan will read "we take pride in your ride"
maybe also very small on the back side the IG icon with Brisks_Polish_Works

phone 208.417.6352
address 3847 E Larkin Ave
Spokane WA 99214
email: BrisksPolish@mailvexo.com

Target Market(s)

all ages , auto enthusiasts

Industry/Entity Type

Automotive

Contact Information for Business Card

the front should have logo, address, phone and email and the back side should have a slogan and text indicating that we offer services on anything including cars, trucks, motorcycles and RVs. slogan will read "we take pride in your ride"

phone 208.417.6352
address 3847 E Larkin Ave
Spokane WA 99214

Colors
000000
ffffff

Requirements
Must have
• bold font and very simple design with good spacing
Nice to have
• anything creative from the designer indicating we service any types of vehicles
Should not have
• any colors ,

```html
<!DOCTYPE html>
<html lang="en">
<head>
<meta charset="utf-8">
<title>Brisk's Polish Works – Business Card</title>
<link rel="stylesheet" href="https://fonts.googleapis.com/css2?family=Roboto+Slab:wght@400;600&display=swap">
<style>
  :root {
    --backdrop: #262626;
    --card: #121212;
    --ink: #ffffff;
    --ink-soft: #e6e6e6;
    --ink-muted: #bdbdbd;
    --card-edge: #2c2c2c;
  }
  * { margin: 0; padding: 0; box-sizing: border-box; }
  html, body {
    width: 1200px; height: 900px; overflow: hidden;
    background: var(--backdrop);
    font-family: "Roboto Slab", Georgia, serif;
    color: var(--ink);
  }
  .canvas {
    width: 1200px; height: 900px;
    display: flex; flex-direction: column; align-items: center; justify-content: center;
    gap: 36px;
  }
  .card {
    position: relative;
    width: 720px; height: 410px;
    background: var(--card);
    border: 1px solid var(--card-edge);
    box-shadow: 0 14px 30px rgba(0,0,0,.45);
  }
  /* Logo side */
  .brand {
    position: absolute; left: 0; right: 0; top: 110px;
    display: flex; align-items: center; justify-content: center; gap: 16px;
  }
  .brand-dot {
    width: 34px; height: 34px; border-radius: 50%;
    background: var(--ink-soft);
  }
  .brand-name {
    font-size: 36px; font-weight: 600; letter-spacing: 1px;
    color: var(--ink-soft); white-space: nowrap;
  }
  .slogan {
    position: absolute; left: 0; right: 0; top: 190px;
    text-align: center; font-size: 20px; font-weight: 400;
    letter-spacing: 1px; color: var(--ink-soft);
  }
  .services {
    position: absolute; left: 0; right: 0; bottom: 70px;
    text-align: center;
    font-size: 17px; font-weight: 400; letter-spacing: 1.5px;
    text-transform: uppercase; white-space: nowrap;
  }
  .social {
    position: absolute; left: 0; right: 0; bottom: 26px;
    display: flex; align-items: center; justify-content: center; gap: 7px;
    font-size: 12px; letter-spacing: .5px; color: var(--ink-muted);
  }
  .social-mark {
    width: 11px; height: 11px; border: 1.5px solid var(--ink-muted); border-radius: 3px;
  }
  /* Contact side */
  .identity {
    position: absolute; right: 340px; top: 148px;
    text-align: right; white-space: nowrap;
  }
  .person-name {
    font-size: 30px; font-weight: 600; letter-spacing: 1px;
    text-transform: uppercase; line-height: 1.1;
  }
  .person-role { font-size: 16px; margin-top: 2px; }
  .divider {
    position: absolute; left: 405px; top: 150px;
    width: 2px; height: 66px; background: var(--ink);
  }
  .contacts {
    position: absolute; left: 432px; top: 160px;
    list-style: none; font-size: 16px; line-height: 22px; white-space: nowrap;
  }
  .contacts li { display: flex; align-items: center; gap: 8px; }
  .contacts svg { width: 11px; height: 11px; flex: none; }
  .address {
    position: absolute; left: 0; right: 0; bottom: 70px;
    text-align: center; font-size: 17px; white-space: nowrap;
  }
</style>
</head>
<body>
<main class="canvas">
  <section class="card card-front">
    <div class="brand">
      <span class="brand-dot"></span>
      <span class="brand-name">Brisk's Polish Works</span>
    </div>
    <p class="slogan">“We take pride in your ride”</p>
    <p class="services">Cars – Trucks – Motorcycles and RVs</p>
    <p class="social"><span class="social-mark"></span>Brisks_Polish_Works</p>
  </section>

  <section class="card card-contact">
    <div class="identity">
      <h1 class="person-name">Daniel Rourke</h1>
      <p class="person-role">Director</p>
    </div>
    <span class="divider"></span>
    <ul class="contacts">
      <li>
        <svg viewBox="0 0 12 12" aria-hidden="true"><path d="M2.5 1l2 2.2-1 1.3c.8 1.6 1.8 2.6 3.4 3.4l1.3-1 2.2 2-1.2 1.6C5 10.2 1.8 7 .9 2.2z" fill="#fff"/></svg>
        208.417.6352
      </li>
      <li>
        <svg viewBox="0 0 12 12" aria-hidden="true"><rect x="1" y="2.5" width="10" height="7" fill="none" stroke="#fff" stroke-width="1.2"/><path d="M1 2.5l5 4 5-4" fill="none" stroke="#fff" stroke-width="1.2"/></svg>
        BrisksPolish@mailvexo.com
      </li>
      <li>
        <svg viewBox="0 0 12 12" aria-hidden="true"><circle cx="6" cy="6" r="5" fill="none" stroke="#fff" stroke-width="1.1"/><ellipse cx="6" cy="6" rx="2.2" ry="5" fill="none" stroke="#fff" stroke-width="1"/><path d="M1 6h10" stroke="#fff" stroke-width="1"/></svg>
        www.BrisksPolish.com
      </li>
    </ul>
    <p class="address">3847 E Larkin Ave Spokane WA 99214</p>
  </section>
</main>
</body>
</html>
```